KRT Project Signage

Need a sign to be displayed in the front of properties currently under Construction or Renovation to advertise our company information. Need it to be Professional and Contemporary. We are a Design/Build Construction Company. Information should include Company Name, email, website, phone number. Attached: Logo and company brochure, also included and inspiration images

```html
<!DOCTYPE html>
<html lang="en">
<head>
<meta charset="utf-8">
<title>KRT Project Signage</title>
<link href="https://fonts.googleapis.com/css2?family=Poppins:wght@400;600;700;800&display=swap" rel="stylesheet">
<style>
  :root {
    --yellow: #f2e534;
    --ink: #1c1c1c;
    --dark: #202020;
    --dark-2: #2c2c2c;
    --grey: #4a4a4a;
    --white: #ffffff;
    --page: #ffffff;
  }
  * { box-sizing: border-box; margin: 0; padding: 0; }
  html, body {
    width: 1200px; height: 3390px; overflow: hidden;
    background: var(--page);
    font-family: "Poppins", sans-serif;
  }
  .sign {
    position: absolute; left: 80px; top: 915px;
    width: 1040px; height: 1560px;
    background: var(--white);
    box-shadow: 0 6px 28px rgba(0,0,0,.18);
    overflow: hidden;
  }
  .brand {
    position: absolute; top: 150px; left: 0; width: 100%;
    display: flex; justify-content: center; align-items: center; gap: 22px;
  }
  .brand-dot { width: 58px; height: 58px; border-radius: 50%; background: var(--yellow); }
  .brand-name {
    font-weight: 600; font-size: 58px; letter-spacing: 3px; color: var(--ink);
  }
  .person {
    position: absolute; top: 350px; width: 100%; text-align: center;
    font-weight: 800; font-size: 92px; line-height: 110px; color: var(--ink);
  }
  .role {
    position: absolute; top: 475px; left: 125px; width: 790px; height: 97px;
    background: var(--yellow); border-radius: 26px;
    text-align: center; font-weight: 400; font-size: 70px; line-height: 97px; color: var(--ink);
  }
  .wave { position: absolute; top: 610px; left: 0; width: 1040px; height: 150px; }
  .backdrop {
    position: absolute; top: 758px; left: 0; width: 1040px; height: 690px;
    background: linear-gradient(180deg, var(--dark) 0%, var(--dark-2) 55%, var(--dark) 100%);
  }
  .contact { position: absolute; left: 0; width: 100%; text-align: center; color: var(--white); }
  .icon {
    position: absolute; left: 487px; width: 66px; height: 66px;
  }
  .address { top: 808px; font-size: 46px; line-height: 60px; }
  .email { top: 1020px; font-size: 46px; line-height: 66px; }
  .web { top: 1177px; font-size: 46px; line-height: 66px; }
  .office {
    top: 1290px; font-weight: 700; font-size: 58px; line-height: 72px;
    display: flex; justify-content: center; align-items: center; gap: 24px;
  }
  .office svg { width: 66px; height: 66px; }
  .base { position: absolute; top: 1443px; left: 0; width: 100%; height: 117px; background: var(--yellow); }
  .mobile {
    position: absolute; top: 1397px; left: 193px; width: 675px; height: 89px;
    background: var(--white); border-radius: 28px;
    display: flex; justify-content: center; align-items: center; gap: 28px;
    font-weight: 700; font-size: 78px; color: var(--ink);
  }
  .mobile svg { width: 62px; height: 62px; }
</style>
</head>
<body>
<main class="sign">
  <div class="brand">
    <span class="brand-dot"></span>
    <span class="brand-name">KRT CONSTRUCTION</span>
  </div>
  <h1 class="person">DORIAN VALE</h1>
  <div class="role">DESIGN &amp; BUILDER</div>

  <svg class="wave" viewBox="0 0 1040 150" preserveAspectRatio="none">
    <path d="M560,62 C760,112 900,92 1040,40 V100 C920,118 780,132 620,84 Z" fill="var(--grey)"/>
    <path d="M0,38 C200,-14 400,-4 620,64 C780,114 920,100 1040,78 V100 C920,118 780,132 620,84 C400,16 200,8 0,62 Z" fill="var(--yellow)"/>
    <path d="M0,62 C200,8 400,16 620,84 C780,132 920,118 1040,100 V150 H0 Z" fill="var(--dark)"/>
  </svg>
  <div class="backdrop" role="img" aria-label="Dimmed photo of a finished interior behind the contact details"></div>

  <svg class="icon" style="top:736px" viewBox="0 0 66 66">
    <circle cx="33" cy="33" r="32" fill="var(--yellow)"/>
    <path d="M33 14c-8 0-14 6-14 13.5C19 37 33 50 33 50s14-13 14-22.5C47 20 41 14 33 14z" fill="none" stroke="var(--ink)" stroke-width="4"/>
    <circle cx="33" cy="28" r="5" fill="none" stroke="var(--ink)" stroke-width="4"/>
  </svg>
  <p class="contact address">4410 Harbor Line Rd., Ste. 12<br>Coral Bay, FL 30918</p>

  <svg class="icon" style="top:946px" viewBox="0 0 66 66">
    <circle cx="33" cy="33" r="32" fill="var(--yellow)"/>
    <rect x="16" y="21" width="34" height="24" rx="3" fill="none" stroke="var(--ink)" stroke-width="4"/>
    <path d="M17 23 L33 36 L49 23 M17 44 L28 33 M49 44 L38 33" fill="none" stroke="var(--ink)" stroke-width="3.5"/>
  </svg>
  <p class="contact email">info@krtbuildco.com</p>

  <svg class="icon" style="top:1096px" viewBox="0 0 66 66">
    <circle cx="33" cy="33" r="32" fill="var(--yellow)"/>
    <g fill="none" stroke="var(--ink)" stroke-width="3">
      <circle cx="33" cy="33" r="17"/>
      <ellipse cx="33" cy="33" rx="8" ry="17"/>
      <path d="M16 33 H50 M19 24 H47 M19 42 H47"/>
    </g>
  </svg>
  <p class="contact web">www.krtbuildco.com</p>

  <div class="contact office">
    <span>Office</span>
    <svg viewBox="0 0 66 66">
      <circle cx="33" cy="33" r="32" fill="var(--yellow)"/>
      <path d="M22 17 l7 0 3 9 -5 4 c2 5 6 9 11 11 l4 -5 9 3 0 7 c0 3 -3 5 -6 5 C31 51 15 35 15 23 c0 -3 3 -6 7 -6z" fill="var(--ink)"/>
    </svg>
    <span>555.310.2284</span>
  </div>

  <div class="base"></div>
  <div class="mobile">
    <svg viewBox="0 0 66 66">
      <path d="M15 8 l10 0 4 13 -7 5 c3 7 9 13 16 16 l5 -7 13 4 0 10 c0 4 -4 7 -8 7 C29 56 9 36 9 16 c0 -4 3 -8 6 -8z" fill="var(--ink)"/>
      <path d="M38 10 a18 18 0 0 1 18 18 M38 20 a8 8 0 0 1 8 8" fill="none" stroke="var(--ink)" stroke-width="4"/>
    </svg>
    <span>555.720.4613</span>
  </div>
</main>
</body>
</html>
```